Business card design for Virtual Assistance company

I need a business card designed for my virtual assistance company. We are a small company who services primarily C-level executive clients. The card needs to be double sided with the following contact information on the back:
Melissa Thornbury
Owner/CEO
info@rkpadvisory.net
www.rkpadvisory.net
555.302.9817

The front side should just have the company name incorporated: "RKP Advisory" and "virtual assistance"

The card should be simplistic, but eye catching and should speak to high level executives. Our primary focus areas consist of executive assistance and government contracting.

Target Market(s)

CEOs and executives

Contact Information for Business Card

see project description. phone, email, website.

Colors

Designer to choose only greyscale colors for use in the design.

```html
<!DOCTYPE html>
<html lang="en">
<head>
<meta charset="utf-8">
<title>RKP Advisory – Business Card</title>
<link href="https://fonts.googleapis.com/css2?family=Crimson+Text:wght@400;600;700&family=Montserrat:wght@400&display=swap" rel="stylesheet">
<style>
  :root {
    --backdrop: #7d6c58;
    --card: #1c1c1c;
    --ink: #ffffff;
    --ink-soft: #e6e6e6;
    --pattern-light: #3a3a3a;
    --pattern-mid: #1e1e1e;
    --pattern-dark: #0a0a0a;
  }
  * { box-sizing: border-box; margin: 0; padding: 0; }
  html, body {
    width: 900px;
    height: 1200px;
    overflow: hidden;
    background: var(--backdrop);
  }
  .stage { position: relative; width: 900px; height: 1200px; }
  .card {
    position: absolute;
    left: 80px;
    width: 742px;
    height: 441px;
    border-radius: 22px;
    background: var(--card);
    box-shadow: 0 6px 14px rgba(0,0,0,.45);
    overflow: hidden;
    color: var(--ink);
  }
  .card--front { top: 131px; }
  .card--back { top: 638px; }

  .company-name {
    position: absolute;
    left: 41px; top: 66px;
    font-family: "Crimson Text", serif;
    font-weight: 600;
    font-size: 47px;
    line-height: 1.1;
    letter-spacing: -0.3px;
  }
  .person-name {
    position: absolute;
    left: 41px; top: 196px;
    font-family: "Crimson Text", serif;
    font-weight: 700;
    font-size: 26px;
    line-height: 1.1;
  }
  .person-title {
    position: absolute;
    left: 41px; top: 232px;
    font-family: "Montserrat", sans-serif;
    font-size: 15px;
    color: var(--ink-soft);
  }
  .contact-list {
    position: absolute;
    left: 43px; top: 287px;
    list-style: none;
    font-family: "Montserrat", sans-serif;
    font-size: 15.5px;
    color: var(--ink-soft);
  }
  .contact-list li {
    display: flex;
    align-items: center;
    gap: 9px;
    height: 28px;
  }
  .contact-list svg { width: 16px; height: 16px; fill: var(--ink); }
  .tagline {
    position: absolute;
    left: 43px; top: 390px;
    font-family: "Crimson Text", serif;
    font-size: 16.5px;
    letter-spacing: 0.3px;
    text-transform: uppercase;
  }
  .brand-initials {
    position: absolute;
    left: 395px; top: 195px;
    width: 325px;
    text-align: center;
    font-family: "Crimson Text", serif;
    font-weight: 600;
    font-size: 150px;
    line-height: 1;
  }
  .back-pattern {
    position: absolute;
    inset: 0;
    background:
      radial-gradient(ellipse at 15% 20%, rgba(255,255,255,.10) 0%, rgba(255,255,255,0) 55%),
      linear-gradient(100deg, var(--pattern-light) 0%, var(--pattern-mid) 40%, var(--pattern-dark) 100%);
  }
  .brand-initials--small {
    position: absolute;
    left: 545px; top: 262px;
    width: 130px;
    text-align: center;
    font-family: "Crimson Text", serif;
    font-weight: 600;
    font-size: 52px;
    line-height: 1;
  }
</style>
</head>
<body>
<main class="stage">
  <section class="card card--front" aria-label="Business card front">
    <h1 class="company-name">RKP Advisory</h1>
    <p class="person-name">Melissa Thornbury</p>
    <p class="person-title">Owner/CEO</p>
    <ul class="contact-list">
      <li>
        <svg viewBox="0 0 24 24" aria-hidden="true"><path d="M6.6 10.8a15.1 15.1 0 0 0 6.6 6.6l2.2-2.2a1 1 0 0 1 1-.25 11.4 11.4 0 0 0 3.6.57 1 1 0 0 1 1 1V20a1 1 0 0 1-1 1A17 17 0 0 1 3 4a1 1 0 0 1 1-1h3.5a1 1 0 0 1 1 1c0 1.25.2 2.45.57 3.57a1 1 0 0 1-.25 1z"/></svg>
        555.302.9817
      </li>
      <li>
        <svg viewBox="0 0 24 24" aria-hidden="true"><path d="M3 5h18v2l-9 6-9-6zM3 9l9 6 9-6v10H3z"/></svg>
        info@rkpadvisory.net
      </li>
      <li>
        <svg viewBox="0 0 24 24" aria-hidden="true"><circle cx="12" cy="12" r="9" fill="none" stroke="#fff" stroke-width="2"/><path d="M3 12h18M12 3c3 3 3 15 0 18M12 3c-3 3-3 15 0 18" fill="none" stroke="#fff" stroke-width="1.6"/></svg>
        www.rkpadvisory.net
      </li>
    </ul>
    <p class="tagline">Virtual Assistance</p>
    <p class="brand-initials">RKP</p>
  </section>

  <section class="card card--back" aria-label="Business card back">
    <div class="back-pattern" role="img" aria-label="Tonal repeating monogram pattern fading from grey to black"></div>
    <p class="brand-initials--small">RKP</p>
  </section>
</main>
</body>
</html>
```